Brightwater Care Partners, LLC Business Card update!

would like a classier business card. Our cards currently just have our logo and contact information. Need better use of color and creativity
Logo attached.

Target Market(s)

Potential clients, contacts, existing clients. We are a consulting company

Industry/Entity Type

Business

Contact Information for Business Card

We like our colors but just have a boring card with our logo and a white background. I want something that stands out.

Colors
ec1f27
757575

Requirements
Must have
• Color to stay consistent. Logo provided
Nice to have
• Just better use of color/ design

```html
<!DOCTYPE html>
<html lang="en">
<head>
<meta charset="utf-8">
<title>Brightwater Care Partners — Business Card</title>
<link rel="stylesheet" href="https://fonts.googleapis.com/css2?family=Michroma&display=swap">
<style>
  :root {
    --brand-pink: #d6136b;
    --brand-grey: #757575;
    --card-white: #ffffff;
    --backdrop: #e4e5e6;
    --ink-white: #ffffff;
  }
  * { box-sizing: border-box; margin: 0; padding: 0; }
  html, body {
    width: 1200px; height: 771px; overflow: hidden;
    background: var(--backdrop);
    font-family: "Michroma", sans-serif;
  }
  .sheet {
    position: relative; width: 1200px; height: 771px;
    display: flex; align-items: center; justify-content: center; gap: 60px;
  }
  .card {
    position: relative; width: 520px; height: 297px;
    background: var(--card-white);
    box-shadow: 0 6px 18px rgba(0,0,0,0.12);
    overflow: hidden;
  }
  /* Front */
  .wordmark {
    display: flex; align-items: center; gap: 14px;
  }
  .wordmark-dot {
    width: 34px; height: 34px; border-radius: 50%;
    background: var(--brand-grey); flex: none;
  }
  .wordmark-name {
    color: var(--brand-pink);
    font-weight: 400;
    line-height: 1.15;
  }
  .card-front .wordmark {
    position: absolute; left: 50%; top: 50%;
    transform: translate(-50%, -50%);
  }
  .card-front .wordmark-name { font-size: 22px; }
  /* Back */
  .band { position: absolute; inset: 0; }
  .card-back .wordmark {
    position: absolute; right: 34px; top: 34px;
  }
  .card-back .wordmark-dot { width: 26px; height: 26px; }
  .card-back .wordmark-name { font-size: 16px; }
  .contact-list {
    position: absolute; left: 26px; top: 150px;
    list-style: none; color: var(--ink-white);
    font-size: 7.5px; letter-spacing: 0.06em; line-height: 14px;
  }
  .contact-list li { display: flex; align-items: center; gap: 7px; }
  .contact-icon {
    width: 9px; height: 9px; border-radius: 50%;
    background: var(--ink-white); flex: none;
  }
  .holder {
    position: absolute; right: 30px; bottom: 22px;
    text-align: right; color: var(--ink-white);
  }
  .holder-name { font-size: 11px; letter-spacing: 0.08em; }
  .holder-title { font-size: 7px; letter-spacing: 0.3em; margin-top: 4px; }
</style>
</head>
<body>
<main class="sheet">
  <section class="card card-front">
    <div class="wordmark">
      <span class="wordmark-dot"></span>
      <span class="wordmark-name">Brightwater<br>Care Partners</span>
    </div>
  </section>

  <section class="card card-back">
    <svg class="band" viewBox="0 0 520 297" preserveAspectRatio="none" aria-hidden="true">
      <path d="M0 112 C 140 104, 300 120, 520 226 L520 236 C 300 132, 140 118, 0 124 Z" fill="var(--brand-grey)"/>
      <path d="M0 132 C 150 124, 300 150, 520 250 L520 297 L0 297 Z" fill="var(--brand-pink)"/>
    </svg>
    <div class="wordmark">
      <span class="wordmark-dot"></span>
      <span class="wordmark-name">Brightwater<br>Care Partners</span>
    </div>
    <ul class="contact-list">
      <li><span class="contact-icon"></span>SUITE # 410, HARBOR BLDG,</li>
      <li><span class="contact-icon" style="visibility:hidden"></span>NY 10217</li>
      <li><span class="contact-icon"></span>212-555-0148</li>
      <li><span class="contact-icon"></span>212-555-0193</li>
      <li><span class="contact-icon"></span>212-555-0177</li>
      <li><span class="contact-icon"></span>INFO@BRIGHTWATERCP.COM</li>
      <li><span class="contact-icon"></span>WWW.BRIGHTWATERCP.COM</li>
    </ul>
    <div class="holder">
      <p class="holder-name">DANIEL REYES</p>
      <p class="holder-title">OWNER / C.E.O</p>
    </div>
  </section>
</main>
</body>
</html>
```